Business Card Design for a Software Startup

We'd like to have a business card design. We already have a logo. Basically what we need is a clean design with name, address, cellphone and phone numbers, e-mail and web site address (front) and a space on the back with our logo with the company name on the right side and some texts on the bottom.
We are a development and consulting company in Brazil with highly qualified team of professionals in Java, iOS and Android development and consulting.

Target Market(s)

CIO, IT managers of mid to big size companies

Industry/Entity Type

Business

```html
<!DOCTYPE html>
<html lang="en">
<head>
<meta charset="utf-8">
<title>Vantri Business Card</title>
<link rel="stylesheet" href="https://fonts.googleapis.com/css2?family=Arimo:wght@400;700&family=Questrial&display=swap">
<style>
  :root {
    --navy: #10335f;
    --brand-blue: #1f6fa8;
    --accent-line: #4fa3d8;
    --ink: #3a3a3a;
    --card: #ffffff;
    --backdrop: #e9e6e1;
  }
  * { box-sizing: border-box; margin: 0; padding: 0; }
  html, body {
    width: 1200px;
    height: 720px;
    overflow: hidden;
    background: var(--backdrop);
  }
  .sheet {
    width: 1200px;
    height: 720px;
    display: flex;
    align-items: center;
    justify-content: center;
    gap: 40px;
  }
  .card {
    position: relative;
    width: 540px;
    height: 309px;
    background: var(--card);
    box-shadow: 0 6px 18px rgba(0, 0, 0, 0.18);
    overflow: hidden;
  }

  /* Front side */
  .front .name-band {
    position: absolute;
    top: 0; left: 0; right: 0;
    height: 58px;
    background: var(--navy);
    color: #fff;
    display: flex;
    align-items: baseline;
    justify-content: center;
    padding-top: 17px;
    font-family: "Arimo", Arial, sans-serif;
  }
  .front .holder-name { font-weight: 700; font-size: 23px; }
  .front .holder-title { font-weight: 400; font-size: 17px; margin-left: 6px; }
  .front .rule {
    position: absolute;
    left: 0; right: 0;
    height: 2px;
    background: var(--accent-line);
  }
  .front .rule.top { top: 63px; }
  .front .rule.bottom { bottom: 55px; }
  .front .brand {
    position: absolute;
    top: 84px;
    left: 0; right: 0;
    display: flex;
    flex-direction: column;
    align-items: center;
    gap: 6px;
  }
  .brand-square {
    width: 54px;
    height: 54px;
    border-radius: 9px;
    background: var(--brand-blue);
  }
  .brand-name {
    font-family: "Arimo", Arial, sans-serif;
    font-weight: 700;
    font-size: 28px;
    line-height: 1;
    color: var(--navy);
    letter-spacing: 1px;
  }
  .contact-row {
    position: absolute;
    top: 184px;
    left: 0; right: 0;
    display: flex;
    justify-content: center;
    gap: 22px;
  }
  .contact {
    font-family: "Questrial", "Century Gothic", sans-serif;
    color: var(--ink);
    font-size: 15px;
    line-height: 1;
    display: flex;
    align-items: center;
    gap: 6px;
  }
  .contact svg { width: 13px; height: 13px; fill: var(--ink); }
  .front .web {
    position: absolute;
    top: 212px;
    left: 0; right: 0;
    text-align: center;
    font-family: "Questrial", "Century Gothic", sans-serif;
    color: var(--ink);
    font-size: 14px;
    letter-spacing: 3px;
  }
  .front .address-band {
    position: absolute;
    bottom: 0; left: 0; right: 0;
    height: 50px;
    background: var(--navy);
    color: #fff;
    font-family: "Questrial", "Century Gothic", sans-serif;
    font-size: 16px;
    display: flex;
    align-items: center;
    justify-content: center;
  }

  /* Back side */
  .back .brand {
    position: absolute;
    top: 70px;
    left: 0; right: 0;
    display: flex;
    align-items: center;
    justify-content: center;
    gap: 16px;
  }
  .back .brand-square { width: 96px; height: 96px; border-radius: 14px; }
  .back .brand-name { font-size: 50px; }
  .back .site {
    position: absolute;
    bottom: 40px;
    right: 56px;
    font-family: "Arimo", Arial, sans-serif;
    font-weight: 700;
    font-size: 19px;
    letter-spacing: 6px;
    color: #444;
  }
  .back .site .site-name { color: var(--brand-blue); }
</style>
</head>
<body>
<main class="sheet">

  <section class="card front" aria-label="Card front">
    <header class="name-band">
      <span class="holder-name">Your Name,</span>
      <span class="holder-title">Title</span>
    </header>
    <div class="rule top"></div>

    <div class="brand">
      <span class="brand-square"></span>
      <span class="brand-name">VANTRI</span>
    </div>

    <div class="contact-row">
      <p class="contact phone">
        <svg viewBox="0 0 16 16" aria-hidden="true"><path d="M4 1l3 3-2 2c1 2 3 4 5 5l2-2 3 3-2 3C7 15 1 9 1 3z"/></svg>
        555-013-2468
      </p>
      <p class="contact mobile">
        <svg viewBox="0 0 16 16" aria-hidden="true"><path d="M4 0h8v16H4z M5 2v10h6V2z" fill-rule="evenodd"/></svg>
        555-019-7531
      </p>
      <p class="contact email">
        <svg viewBox="0 0 16 16" aria-hidden="true"><path d="M1 3h14v10H1z M2 4v1l6 4 6-4V4z" fill-rule="evenodd"/></svg>
        yourname@vantri.com
      </p>
    </div>
    <p class="web">www.vantri.com</p>

    <div class="rule bottom"></div>
    <footer class="address-band">Door No. Street Name City Name, State, Zip Code.</footer>
  </section>

  <section class="card back" aria-label="Card back">
    <div class="brand">
      <span class="brand-square"></span>
      <span class="brand-name">VANTRI</span>
    </div>
    <p class="site">www.<span class="site-name">vantri</span>.com</p>
  </section>

</main>
</body>
</html>
```